Flyer for the Radiant Harvest Worship Day

I am looking to create a flyer for a one day prayer retreat our church is organizing.
This flyer will be posted on social media, websites and will also be printed so it can be mailed to people.
I am looking for something professional, with good use of our logo and band colors (logo colors).
I am counting on the designer's skill, creativity, art and knowledge of media communication to produce a flyer that will effectively and quickly convey the message we are trying to spread.
CONTENT OF THE FLYER:
Event title: Radiant Harvest Worship Day
Date: Tuesday July 2nd, 2019
Time: 11:00AM - 7:00PM
Belmora Hotel, 4875 Wexley Avenue, Portland, Maine 04102 (Room: Juniper)
Event Key words to highlight what the event is about: Prayer, Sharing the Word, Panel discussion, prophecy, Impartation.
Key phrases:
A one day prayer retreat.
Jesus Chris is Lord
Contact info:
www.tolvex.org
Phone: 207 555 3184
Email: contact@brookhavenfold.org

```html
<!DOCTYPE html>
<html lang="en">
<head>
<meta charset="utf-8">
<title>Radiant Harvest Worship Day</title>
<link href="https://fonts.googleapis.com/css2?family=Cinzel:wght@400;600;700&display=swap" rel="stylesheet">
<style>
  :root {
    --page: #4a4a4a;
    --ink: #14151c;
    --ink-soft: #1c1d26;
    --gold: #f29a1f;
    --cream: #f3efe6;
    --white: #ffffff;
  }
  * { margin: 0; padding: 0; box-sizing: border-box; }
  html, body { width: 1200px; height: 1200px; overflow: hidden; background: var(--page); }
  body { font-family: "Cinzel", serif; color: var(--cream); }

  .flyer {
    position: absolute; left: 190px; top: 20px;
    width: 916px; height: 1297px;
    transform: scale(0.8944); transform-origin: 0 0;
    background: var(--ink); overflow: hidden;
  }
  .flyer__photo {
    position: absolute; left: 38px; top: 290px; width: 840px; height: 820px;
    background:
      radial-gradient(ellipse 46% 36% at 50% 40%, #b8b2a6 0%, #7c776e 35%, rgba(40,40,46,0.6) 70%, rgba(20,21,28,0) 100%);
  }
  .flyer__frame {
    position: absolute; left: 38px; top: 41px; right: 38px; bottom: 41px;
    border: 2px solid var(--gold);
  }
  .flyer__kicker {
    position: absolute; top: 68px; width: 100%; text-align: center;
    font-size: 36px; font-weight: 400; color: var(--white); letter-spacing: 1px;
  }
  .flyer__headline {
    position: absolute; top: 152px; width: 100%; text-align: center;
    font-size: 50px; font-weight: 600; color: var(--white); line-height: 1;
  }
  .flyer__tagline {
    position: absolute; top: 198px; width: 100%; text-align: center;
    font-size: 73px; font-weight: 700; color: var(--gold); line-height: 1;
  }

  .event-info {
    position: absolute; left: 112px; top: 741px; width: 691px; height: 127px;
    background: rgba(16,17,23,0.88); display: flex; align-items: center;
  }
  .event-info__when { padding-left: 20px; width: 333px; }
  .event-info__date { font-size: 25px; color: var(--white); }
  .event-info__time { font-size: 36px; color: var(--white); margin-top: 4px; }
  .event-info__divider { width: 1px; height: 80px; background: var(--gold); margin-right: 16px; }
  .event-info__where { font-size: 16px; line-height: 19px; color: var(--white); margin-top: -18px; }

  .highlights {
    position: absolute; left: 117px; top: 896px; width: 682px; height: 168px;
    border: 2px solid var(--white); border-radius: 10px; display: flex; padding-top: 20px;
  }
  .highlights__col { list-style: none; padding-left: 34px; width: 366px; }
  .highlights__col + .highlights__col { width: auto; padding-left: 56px; }
  .highlights__divider { width: 1px; height: 110px; background: var(--gold); margin-top: 8px; }
  .highlights__item { display: flex; align-items: center; gap: 12px; font-size: 26px; color: var(--white); height: 38px; }
  .highlights__tick { width: 26px; height: 22px; flex: none; }

  .brand { position: absolute; left: 64px; top: 1165px; }
  .brand__mark { display: flex; align-items: center; gap: 8px; }
  .brand__dot { width: 10px; height: 10px; border-radius: 50%; background: var(--gold); }
  .brand__name { font-size: 41px; font-weight: 400; color: var(--white); line-height: 1; }

  .call {
    position: absolute; left: 255px; top: 1125px; display: flex; align-items: center; gap: 18px;
  }
  .call__badge {
    background: var(--gold); color: var(--ink); font-size: 36px; font-weight: 600;
    border-radius: 8px; padding: 0 10px; height: 42px; line-height: 46px;
  }
  .call__phone { font-size: 47px; color: var(--white); }
  .contact {
    position: absolute; left: 260px; top: 1198px; display: flex; gap: 24px; align-items: center;
    font-size: 18px; color: var(--white);
  }
  .contact__item { display: flex; align-items: center; gap: 12px; }
  .contact__icon { width: 16px; height: 16px; }
</style>
</head>
<body>
<main class="flyer">
  <div class="flyer__photo" role="img" aria-label="Photograph of hands clasped in prayer"></div>
  <div class="flyer__frame"></div>

  <h2 class="flyer__kicker">Radiant Harvest Worship Day</h2>
  <h1 class="flyer__headline">A ONE DAY PRAYER RETREAT</h1>
  <p class="flyer__tagline">Jesus Chris is Lord</p>

  <section class="event-info">
    <div class="event-info__when">
      <p class="event-info__date">Tuesday July 2nd, 2019</p>
      <p class="event-info__time">11:00AM - 7:00PM</p>
    </div>
    <div class="event-info__divider"></div>
    <p class="event-info__where">Belmora Hotel, 4875 Wexley Avenue,<br>Portland, Maine 04102<br>(Room: Juniper)</p>
  </section>

  <section class="highlights">
    <ul class="highlights__col">
      <li class="highlights__item"><svg class="highlights__tick" viewBox="0 0 26 22"><polyline points="2,12 9,19 24,3" fill="none" stroke="#f29a1f" stroke-width="4" stroke-linecap="round" stroke-linejoin="round"/></svg>Prayer</li>
      <li class="highlights__item"><svg class="highlights__tick" viewBox="0 0 26 22"><polyline points="2,12 9,19 24,3" fill="none" stroke="#f29a1f" stroke-width="4" stroke-linecap="round" stroke-linejoin="round"/></svg>Sharing the Word</li>
      <li class="highlights__item"><svg class="highlights__tick" viewBox="0 0 26 22"><polyline points="2,12 9,19 24,3" fill="none" stroke="#f29a1f" stroke-width="4" stroke-linecap="round" stroke-linejoin="round"/></svg>Panel discussion</li>
    </ul>
    <div class="highlights__divider"></div>
    <ul class="highlights__col">
      <li class="highlights__item"><svg class="highlights__tick" viewBox="0 0 26 22"><polyline points="2,12 9,19 24,3" fill="none" stroke="#f29a1f" stroke-width="4" stroke-linecap="round" stroke-linejoin="round"/></svg>prophecy</li>
      <li class="highlights__item"><svg class="highlights__tick" viewBox="0 0 26 22"><polyline points="2,12 9,19 24,3" fill="none" stroke="#f29a1f" stroke-width="4" stroke-linecap="round" stroke-linejoin="round"/></svg>Impartation</li>
    </ul>
  </section>

  <div class="brand">
    <div class="brand__mark"><span class="brand__dot"></span><span class="brand__name">TOLVEX</span></div>
  </div>

  <div class="call">
    <span class="call__badge">CALL US NOW</span>
    <span class="call__phone">207 555 3184</span>
  </div>
  <div class="contact">
    <span class="contact__item">
      <svg class="contact__icon" viewBox="0 0 16 16"><rect x="1" y="3" width="14" height="10" fill="#f29a1f"/><polyline points="1,3 8,9 15,3" fill="none" stroke="#14151c" stroke-width="1.5"/></svg>
      CONTACT@BROOKHAVENFOLD.ORG
    </span>
    <span class="contact__item">
      <svg class="contact__icon" viewBox="0 0 16 16"><circle cx="8" cy="8" r="6.5" fill="none" stroke="#f29a1f" stroke-width="2"/><line x1="1.5" y1="8" x2="14.5" y2="8" stroke="#f29a1f" stroke-width="1.5"/><ellipse cx="8" cy="8" rx="2.5" ry="6.5" fill="none" stroke="#f29a1f" stroke-width="1.5"/></svg>
      WWW.TOLVEX.ORG
    </span>
  </div>
</main>
</body>
</html>
```